Edgy book cover - contemporary fiction

A book cover design for a first-time author. The book is being self-published, but needs to stand out as a quality product amongst a huge number of self-published titles hitting the market.

About the book
“Pebbles Under Water” is a collection of eleven fictional short stories, set in the the turbulent economic times of The Great Recession (Or the Global Financial Crisis). The stories are about ordinary people and their struggles and hopes, as they cope with the circumstances that are dealt them: losing their jobs and homes, helping friends in trouble, making their own success, having to move across town or across the world to survive, having to go back to work after losing their retirement savings.

The book is being published as an e-book only at this stage. The graphic will be viewed as an icon on the zorbex lumora store (and similar stores such as Plover vreads), and as a larger image on the book's own page. In future, the cover may be used in a print version.

I expect to be challenged and stimulated along the way as I don’t have a firm view of what the final cover will look like – it really is up to you to wow me. I value your time and as such I will commit to giving each designer feedback.

Required Deliverables

Although you need only submit the book cover at the design stage the required project deliverables are:
- Book Front Cover - colour. Main focus
- Other versions once finalised:
- Colour image image 928px wide by 1250px high, at 150ppi,
- B&W image 96ppi B/W, and it will resize automatically to 600px by 800px, which is perfect for the inside Lumora cover.
- 6 by 4 inch postcards and A4 posters for promotional purposes
- Final tag-line applied to all of the above
- Front, back and spine book cover design for future printing of physical book, size 5.25 inches by 8 inches. Zorbex Pagewell template available when number of pages has been finalised.
- At least 2 iterations of the winning design

Target Market(s)

The target for this book is a broad, educated middle-class audience, say over age 30, for whom home, mortgage and job are real concerns.

Industry/Entity Type

Printing

Requirements
Must have
• The cover needs to be edgy but not overdone. Less is more in this case. Think about the target audience and their tastes. I think the title gives lots of creative possibility, so please be creative and clever. I’d like people to look at the cover and think “Cool/Clever cover – I’d better read this”. Be original yet keep the end product accessible.

There will be a tag-line on the cover somewhere. Where you locate it is up to you, but you need to leave space for it. For the time being please use the text “Songs from Narrow Rooms ” – but this may change by the end of the project.

The following text of title, tagline and author

Pebbles Under Water
Songs from Narrow Rooms
Neil Ashbury

Purely as guidance to my taste, some book covers I like are:

http://lnkmo.example/qa1rt
http://lnkmo.example/k4p2z
http://lnkmo.example/bhe7m
http://lnkmo.example/x9dwo
http://lnkmo.example/r3fuy
http://lnkmo.example/j8cns
Should not have
• Please avoid clichés and being “overly busy”. Although the book is to be self published on a low budget it shouldn’t look like that. If the cover would look right on a popular mass fiction title then it is probably not right for me.

The design should not use a cliched "happy families" house image.

It needs not to look like it's based on a book cover template from a self-publishing house.

Some examples of book covers I don’t like are :

http://lnkmo.example/p2gke
http://lnkmo.example/m7ylh
http://lnkmo.example/t5awq
http://lnkmo.example/f1zbv
http://lnkmo.example/d6oxs

```html
<!DOCTYPE html>
<html lang="en">
<head>
<meta charset="utf-8">
<title>Pebbles Under Water – Neil Ashbury</title>
<link rel="stylesheet" href="https://fonts.googleapis.com/css2?family=Jost:wght@300;400&display=swap">
<style>
  :root {
    --paper: #ffffff;
    --frame: #3a3a3a;
    --ink: #1a1a1a;
    --grey-text: #7a7a7a;
    --city-dark: #2b2d2a;
    --city-mid: #7d8479;
    --city-light: #d9ddd2;
  }
  html, body {
    margin: 0;
    padding: 0;
    width: 842px;
    height: 1200px;
    overflow: hidden;
    background: var(--paper);
  }
  .cover {
    position: relative;
    width: 842px;
    height: 1200px;
    background: var(--paper);
    font-family: "Jost", "Futura", sans-serif;
  }
  .cover-frame {
    position: absolute;
    left: 68px;
    top: 50px;
    width: 701px;
    height: 1084px;
    border: 1px solid var(--frame);
    box-sizing: border-box;
  }
  .city-window {
    position: absolute;
    left: 0;
    top: 0;
    width: 842px;
    height: 1200px;
  }
  .author {
    position: absolute;
    left: 114px;
    top: 72px;
    margin: 0;
    font-weight: 300;
    font-size: 90px;
    line-height: 1;
    letter-spacing: 5px;
    color: var(--grey-text);
    white-space: nowrap;
  }
  .title {
    position: absolute;
    left: 112px;
    top: 208px;
    margin: 0;
    font-weight: 300;
    font-size: 90px;
    line-height: 82px;
    letter-spacing: 1px;
    text-transform: uppercase;
    color: var(--ink);
    white-space: nowrap;
  }
  .title span { display: block; }
  .tagline {
    position: absolute;
    left: 116px;
    top: 490px;
    margin: 0;
    font-weight: 300;
    font-size: 50px;
    line-height: 1;
    color: var(--grey-text);
    white-space: nowrap;
  }
</style>
</head>
<body>
  <main class="cover">
    <svg class="city-window" viewBox="0 0 842 1200" role="img" aria-label="Night photograph of city office towers seen from above, revealed through a torn opening">
      <defs>
        <linearGradient id="city-tone" x1="1" y1="0" x2="0" y2="1">
          <stop offset="0" stop-color="var(--city-light)"/>
          <stop offset="0.35" stop-color="var(--city-mid)"/>
          <stop offset="0.7" stop-color="var(--city-dark)"/>
          <stop offset="1" stop-color="#6b5f55"/>
        </linearGradient>
      </defs>
      <path fill="url(#city-tone)" d="M769 388 L748 398 L722 418 L696 432 L670 452 L662 492 L656 540 L642 568 L612 592 L590 632 L560 662 L522 688 L476 700 L444 728 L410 770 L378 798 L342 804 L318 814 L346 830 L330 862 L302 902 L274 958 L252 1010 L238 1076 L232 1134 L769 1134 Z"/>
    </svg>
    <div class="cover-frame"></div>
    <p class="author">Neil Ashbury</p>
    <h1 class="title"><span>Pebbles</span><span>Under Water</span></h1>
    <p class="tagline">Songs from Narrow Rooms</p>
  </main>
</body>
</html>
```